Small Business Broker Business Card Design

A business card design for a small business brokerage, which is a financial service, not unlike real estate brokerage, but for small businesses such as laundromats, pizza shops, restaurants, cleaners etc. The designs should all be simple, more conservative in nature, using the colors and font of the logo. Again, think real estate Brokerage as a business context
Contact Information for Business Card
Name: Glen R. Harlow. Title: Small Business Advisor. Email: g.harlow@bayfieldcapitalworks.example. Mobile: (555) 274-3918. Office: (555) 806-2147. www.bayfieldcapitalworks.example

```html
<!DOCTYPE html>
<html lang="en">
<head>
<meta charset="utf-8">
<title>Bayfield Capital Works — Business Card</title>
<link rel="stylesheet" href="https://fonts.googleapis.com/css2?family=Montserrat:wght@600&family=Roboto+Condensed:wght@400;700&family=Roboto:wght@400&display=swap">
<style>
  :root {
    --stage: #2b2e33;
    --card: #1d1d1f;
    --card-edge: #111113;
    --green: #8dc63f;
    --blue: #1f4e9c;
    --white: #f2f2f2;
    --muted: #9a9a9a;
    --pattern-dark: #151517;
    --pattern-light: #5a5a5e;
  }
  * { box-sizing: border-box; margin: 0; padding: 0; }
  html, body { width: 1200px; height: 780px; overflow: hidden; }
  body {
    background: var(--stage);
    display: flex;
    align-items: center;
    justify-content: center;
    gap: 48px;
  }
  .card {
    position: relative;
    width: 540px;
    height: 310px;
    border-radius: 22px;
    background: var(--card);
    box-shadow: 0 3px 0 var(--card-edge), 0 6px 0 var(--card-edge), 0 18px 40px rgba(0,0,0,.45);
    overflow: hidden;
  }

  /* Front */
  .brand {
    position: absolute;
    top: 46px;
    right: 40px;
    text-align: right;
  }
  .brand__name {
    font-family: "Montserrat", sans-serif;
    font-weight: 600;
    font-size: 21px;
    letter-spacing: .06em;
    text-transform: uppercase;
    color: var(--blue);
    white-space: nowrap;
  }
  .brand__tagline {
    margin-top: 6px;
    font-family: "Montserrat", sans-serif;
    font-weight: 600;
    font-size: 9.5px;
    letter-spacing: .12em;
    text-transform: uppercase;
    color: var(--green);
    white-space: nowrap;
  }
  .person {
    position: absolute;
    left: 36px;
    top: 150px;
    width: 196px;
  }
  .person__name {
    font-family: "Roboto Condensed", sans-serif;
    font-weight: 700;
    font-size: 30px;
    color: var(--green);
    line-height: 1;
    white-space: nowrap;
  }
  .person__title {
    margin-top: 8px;
    font-family: "Roboto Condensed", sans-serif;
    font-weight: 400;
    font-size: 16px;
    color: var(--white);
  }
  .divider {
    position: absolute;
    left: 246px;
    top: 176px;
    width: 1px;
    height: 96px;
    background: linear-gradient(to bottom, transparent, var(--muted), transparent);
  }
  .contacts {
    position: absolute;
    left: 262px;
    top: 176px;
    list-style: none;
    font-family: "Roboto", sans-serif;
    font-size: 12px;
    color: var(--white);
  }
  .contacts li {
    display: flex;
    align-items: center;
    gap: 9px;
    height: 24px;
    white-space: nowrap;
  }
  .contacts svg { width: 13px; height: 13px; flex: none; }

  /* Back */
  .card--back .pattern {
    position: absolute;
    inset: 0;
    background: linear-gradient(115deg, var(--pattern-dark) 0%, var(--card) 55%, var(--pattern-light) 100%);
  }
  .card--back .brand {
    top: auto;
    right: auto;
    left: 50%;
    bottom: 36px;
    transform: translateX(-50%);
    text-align: center;
  }
  .card--back .brand__name { font-size: 12px; }
  .card--back .brand__tagline { font-size: 6px; margin-top: 4px; }
</style>
</head>
<body>

  <section class="card card--front">
    <div class="brand">
      <p class="brand__name">Bayfield Capital Works, Inc</p>
      <p class="brand__tagline">Steady guidance for every main street sale</p>
    </div>

    <div class="person">
      <p class="person__name">Glen R. Harlow</p>
      <p class="person__title">Small Business Advisor</p>
    </div>

    <div class="divider"></div>

    <ul class="contacts">
      <li>
        <svg viewBox="0 0 14 14" aria-hidden="true"><rect x="3.5" y="1" width="7" height="12" rx="1.5" fill="none" stroke="var(--blue)" stroke-width="1.4"/></svg>
        (555) 274-3918
      </li>
      <li>
        <svg viewBox="0 0 14 14" aria-hidden="true"><path d="M3 1.5l2.2 2.6-1.3 1.5c.8 1.8 2.3 3.3 4.1 4.1l1.5-1.3 2.6 2.2-1.2 1.8C6.3 12.3 1.7 7.7 1.2 2.7z" fill="var(--green)"/></svg>
        (555) 806-2147
      </li>
      <li>
        <svg viewBox="0 0 14 14" aria-hidden="true"><circle cx="7" cy="7" r="6" fill="var(--blue)"/><path d="M1 7h12M7 1c-2.4 3.5-2.4 8.5 0 12M7 1c2.4 3.5 2.4 8.5 0 12" stroke="var(--card)" stroke-width=".9" fill="none"/></svg>
        www.bayfieldcapitalworks.example
      </li>
      <li>
        <svg viewBox="0 0 14 14" aria-hidden="true"><rect x="1" y="3" width="12" height="9" rx="1" fill="var(--green)"/><path d="M1.5 3.5L7 8l5.5-4.5" stroke="var(--card)" stroke-width="1.1" fill="none"/></svg>
        g.harlow@bayfieldcapitalworks.example
      </li>
    </ul>
  </section>

  <section class="card card--back">
    <div class="pattern" role="img" aria-label="Repeating pattern of dark chevron stripes fading to silver toward one corner"></div>
    <div class="brand">
      <p class="brand__name">Bayfield Capital Works, Inc</p>
      <p class="brand__tagline">Steady guidance for every main street sale</p>
    </div>
  </section>

</body>
</html>
```